Push notification screens at app start up

We have an existing news publication app platform and are adding categories to push notifications.

We need two screens designed (each for Zorbel, Quillet and Android for a total of 6d) that show when the app is first launched.

The workflow of our app:
0. app launch screen while webservices run (no work needed)
1. information screen to the user promoting the benefits of push notification with "Next" button. (see concept attached)
2. Push categories selection screen. This will have list of category types, with on/off switch.

"Select the categories that you wish to receive occasional notices:
Breaking News (on/off switch)
Local News (on/off switch)
Sports (on/off switch)
Local Events (on/off switch)
Weather Alerts (on/off switch)
Local Deals (on/off switch)"

"Enable these categories on the next screen."
"Next" button

Background:
When I was looking around at app designs, I came across this one (http://www.plinthworks.example/design/7719034) and I really liked it. We obviously have different features on our screen, but I’d like to have this same feel. The colors used in this design are perfect.

UPDATE: I do not mean to limit your design to match the layout as the one mentioned above. Please use your creativity for the layout.

Our standard font in Helvetica Neue.

Notes:
- our app is developed for all phone devices from Zorbel 4 to Zorbel 6, so designs should be thoughtful of vertical scrolling if needed.
- our app is developed for Quillets, so we'll need designs completed as well. (We can finalize Zorbel design first, then translate the design to Quillet.)
- our app is developed for Android phones (not tablets), so we'll need designs completed as well. (We can finalize iOS design first, then translater to Android UI design guidelines).

We hope to establish a good on-going relationship with the designer for as-needed work in the future.

News

• Helvetica Neue

• Clean designs. No clutter.
• We would likely go with the standard on/off switches for both iOS and Android, but are open to small custom variations.

```html
<!DOCTYPE html>
<html lang="en">
<head>
<meta charset="utf-8">
<title>Notifications</title>
<link rel="stylesheet" href="https://fonts.googleapis.com/css2?family=Arimo:wght@400;700&display=swap">
<style>
  :root {
    --brand-blue: #1f6ff2;
    --switch-blue: #2a6fe8;
    --page-bg: #ffffff;
    --gap-bg: #f6f6f6;
    --divider: #e3e3e3;
    --label: #555a5e;
    --icon: #8a8d90;
    --body-text: #4a4a4a;
    --switch-border: #d8d8d8;
    --white: #ffffff;
  }
  * { box-sizing: border-box; margin: 0; padding: 0; }
  html, body { width: 675px; height: 1200px; overflow: hidden; background: var(--page-bg); }
  body { font-family: "Arimo", "Helvetica Neue", Helvetica, Arial, sans-serif; position: relative; }

  .app-header { position: absolute; top: 0; left: 0; width: 675px; height: 140px; background: var(--brand-blue); color: var(--white); }
  .status-bar { position: absolute; top: 0; left: 0; width: 100%; height: 40px; font-size: 22px; }
  .status-bar .carrier { position: absolute; left: 10px; top: 8px; display: flex; align-items: center; gap: 8px; }
  .status-bar .time { position: absolute; left: 0; right: 0; top: 8px; text-align: center; font-weight: 700; }
  .status-bar .battery { position: absolute; right: 12px; top: 8px; display: flex; align-items: center; gap: 8px; }
  .nav-bar { position: absolute; top: 40px; left: 0; width: 100%; height: 100px; }
  .nav-bar .back { position: absolute; left: 24px; top: 30px; }
  .nav-bar .title { position: absolute; left: 0; right: 0; top: 28px; text-align: center; font-size: 36px; font-weight: 700; }

  .top-gap { position: absolute; top: 140px; left: 0; width: 675px; height: 44px; background: var(--gap-bg); border-bottom: 2px solid var(--divider); }

  .category-list { position: absolute; top: 184px; left: 0; width: 675px; list-style: none; }
  .category-row { position: relative; height: 99px; border-bottom: 2px solid var(--divider); display: flex; align-items: center; }
  .category-row .row-icon { position: absolute; left: 27px; top: 31px; }
  .category-row .label { position: absolute; left: 101px; font-size: 29px; font-weight: 700; color: var(--label); }
  .switch { position: absolute; left: 567px; top: 22px; width: 94px; height: 54px; border-radius: 27px; border: 2px solid var(--switch-border); background: var(--white); }
  .switch .knob { position: absolute; top: 1px; left: 1px; width: 48px; height: 48px; border-radius: 50%; background: var(--white); box-shadow: 0 2px 5px rgba(0,0,0,0.3); }
  .switch.is-on { background: var(--switch-blue); border-color: var(--switch-blue); }
  .switch.is-on .knob { left: 41px; }

  .footnote { position: absolute; top: 850px; left: 104px; width: 467px; text-align: center; font-size: 19.5px; line-height: 25px; color: var(--body-text); }
</style>
</head>
<body>
  <header class="app-header">
    <div class="status-bar">
      <div class="carrier">
        <svg width="78" height="14" viewBox="0 0 78 14" aria-hidden="true">
          <circle cx="7" cy="7" r="6" fill="#fff"/><circle cx="23" cy="7" r="6" fill="#fff"/><circle cx="39" cy="7" r="6" fill="#fff"/>
          <circle cx="55" cy="7" r="5.3" fill="none" stroke="#fff" stroke-width="1.4"/><circle cx="71" cy="7" r="5.3" fill="none" stroke="#fff" stroke-width="1.4"/>
        </svg>
        <span>NORA</span>
        <svg width="26" height="20" viewBox="0 0 26 20" aria-hidden="true">
          <path d="M1 7 A17 17 0 0 1 25 7" fill="none" stroke="#fff" stroke-width="2.6"/>
          <path d="M5.5 11 A11 11 0 0 1 20.5 11" fill="none" stroke="#fff" stroke-width="2.6"/>
          <path d="M13 19 L9 14.5 A6 6 0 0 1 17 14.5 Z" fill="#fff"/>
        </svg>
      </div>
      <div class="time">4:21 PM</div>
      <div class="battery">
        <span>100%</span>
        <svg width="46" height="20" viewBox="0 0 46 20" aria-hidden="true">
          <rect x="1" y="1" width="40" height="18" rx="3" fill="none" stroke="#fff" stroke-width="2"/>
          <rect x="4" y="4" width="34" height="12" rx="1" fill="#fff"/>
          <rect x="42" y="6" width="3" height="8" rx="1" fill="#fff"/>
        </svg>
      </div>
    </div>
    <div class="nav-bar">
      <svg class="back" width="24" height="38" viewBox="0 0 24 38" aria-label="Back" role="img">
        <path d="M20 3 L5 19 L20 35" fill="none" stroke="#fff" stroke-width="5" stroke-linecap="round" stroke-linejoin="round"/>
      </svg>
      <div class="title">Notifications</div>
    </div>
  </header>

  <div class="top-gap"></div>

  <ul class="category-list">
    <li class="category-row"><svg class="row-icon" width="38" height="36" viewBox="0 0 38 36" aria-hidden="true"><rect x="1.5" y="1.5" width="35" height="33" fill="none" stroke="#8a8d90" stroke-width="2"/><rect x="6" y="7" width="10" height="9" fill="#8a8d90"/><path d="M19 8h13M19 12h13M19 16h13M6 21h26M6 25h26M6 29h26" stroke="#8a8d90" stroke-width="2"/></svg><span class="label">Breaking News</span><span class="switch"><span class="knob"></span></span></li>
    <li class="category-row"><svg class="row-icon" width="38" height="36" viewBox="0 0 38 36" aria-hidden="true"><rect x="1.5" y="1.5" width="35" height="33" fill="none" stroke="#8a8d90" stroke-width="2"/><rect x="6" y="7" width="10" height="9" fill="#8a8d90"/><path d="M19 8h13M19 12h13M19 16h13M6 21h26M6 25h26M6 29h26" stroke="#8a8d90" stroke-width="2"/></svg><span class="label">Local News</span><span class="switch is-on"><span class="knob"></span></span></li>
    <li class="category-row"><svg class="row-icon" width="38" height="36" viewBox="0 0 38 36" aria-hidden="true"><rect x="1.5" y="1.5" width="35" height="33" fill="none" stroke="#8a8d90" stroke-width="2"/><rect x="6" y="7" width="10" height="9" fill="#8a8d90"/><path d="M19 8h13M19 12h13M19 16h13M6 21h26M6 25h26M6 29h26" stroke="#8a8d90" stroke-width="2"/></svg><span class="label">Sports</span><span class="switch"><span class="knob"></span></span></li>
    <li class="category-row"><svg class="row-icon" width="38" height="36" viewBox="0 0 38 36" aria-hidden="true"><rect x="1.5" y="1.5" width="35" height="33" fill="none" stroke="#8a8d90" stroke-width="2"/><rect x="6" y="7" width="10" height="9" fill="#8a8d90"/><path d="M19 8h13M19 12h13M19 16h13M6 21h26M6 25h26M6 29h26" stroke="#8a8d90" stroke-width="2"/></svg><span class="label">Local Events</span><span class="switch"><span class="knob"></span></span></li>
    <li class="category-row"><svg class="row-icon" width="38" height="36" viewBox="0 0 38 36" aria-hidden="true"><rect x="1.5" y="1.5" width="35" height="33" fill="none" stroke="#8a8d90" stroke-width="2"/><rect x="6" y="7" width="10" height="9" fill="#8a8d90"/><path d="M19 8h13M19 12h13M19 16h13M6 21h26M6 25h26M6 29h26" stroke="#8a8d90" stroke-width="2"/></svg><span class="label">Weather Alerts</span><span class="switch"><span class="knob"></span></span></li>
    <li class="category-row"><svg class="row-icon" width="38" height="36" viewBox="0 0 38 36" aria-hidden="true"><rect x="1.5" y="1.5" width="35" height="33" fill="none" stroke="#8a8d90" stroke-width="2"/><rect x="6" y="7" width="10" height="9" fill="#8a8d90"/><path d="M19 8h13M19 12h13M19 16h13M6 21h26M6 25h26M6 29h26" stroke="#8a8d90" stroke-width="2"/></svg><span class="label">Local Deals</span><span class="switch"><span class="knob"></span></span></li>
  </ul>

  <p class="footnote">Lorem Ipsum is simply dummy text of the printing and typesetting industry. Lorem Ipsum has been the industry's standard dummy text ever since the 1500s, when an un-known printer took a galley of type and scrambled it to make a type specimen book.</p>
</body>
</html>
```